Shopping centre customer engagement software website

We need a multi page site with :

*What we do.
*How it works.
*Benefits
* Case study
* Testimonial
* Business login (we provide link to business portal)
* Consumer login (we provide link to consumer site)
* Book a demo
* Contact us

We want it to be clean and crisp and very self explanatory with little clutter. We are thinking white but are open to what ever looks the best.
Updates

Wordpress is preferred

Need extra days to review

Target Market(s)

Shopping centre managers and retail property companies

Coding

Coded - Design and coding required

Number of Pages Required

5+ page

Font styles to use
Sans Serif

Colors
ffffff

Requirements
Must have
• As listed above and must be responsive! Checkout our existing site for the text to be included (will be edited but it’ll give you an idea) www.vostrelink.com

```html
<!DOCTYPE html>
<html lang="en">
<head>
<meta charset="utf-8">
<title>Vostrelink – Shopping Centre Engagement</title>
<link href="https://fonts.googleapis.com/css2?family=Ubuntu:wght@300;400;500;700&display=swap" rel="stylesheet">
<style>
:root{
  --cyan:#5cc8dc;
  --ink:#111;
  --text:#444;
  --light:#f1f1f1;
  --white:#fff;
  --dark:#141414;
  --card:#1b2328;
  --orb:#b9bec2;
  --btn:#3b3b3b;
  --sky:#8fcde3;
}
*{box-sizing:border-box;margin:0;padding:0}
html,body{width:1200px;height:3766px;overflow:hidden}
body{font-family:'Ubuntu',sans-serif;color:var(--text);position:relative;background:var(--white)}
.abs{position:absolute}
section,footer{position:absolute;left:0;width:1200px}
.title{position:absolute;left:0;width:1200px;text-align:center;font-weight:500;font-size:34px;color:var(--ink);letter-spacing:.5px}
.orb{position:absolute;left:582px;width:36px;height:36px;border-radius:50%;background:var(--orb)}
/* hero */
.hero{top:0;height:540px}
.hero-photo{position:absolute;inset:0;background:linear-gradient(180deg,#1f4f86 0%,#4f7aa2 35%,#a58a66 65%,#6b5a45 100%)}
.nav{position:absolute;top:50px;left:0;width:1200px;height:30px}
.nav a{position:absolute;top:6px;color:var(--white);font-size:15px;font-weight:500;text-decoration:none;letter-spacing:.3px}
.nav a.active{border-bottom:2px solid var(--cyan);padding-bottom:6px}
.brand{position:absolute;left:540px;top:-20px;width:120px;text-align:center;color:var(--white)}
.brand .dot{display:block;margin:0 auto 6px;width:40px;height:40px;border-radius:50%;background:var(--orb)}
.brand span{font-size:15px;font-weight:500;letter-spacing:1px}
.search{position:absolute;left:1026px;top:0;width:32px;height:32px;border-radius:50%;background:var(--cyan)}
.hero h1{position:absolute;top:272px;left:0;width:1200px;text-align:center;color:var(--white);font-weight:400;font-size:29px;line-height:38px}
.btn-cyan{position:absolute;background:var(--cyan);color:var(--white);font-size:14px;font-weight:500;text-align:center;letter-spacing:.5px}
.dots{position:absolute;top:478px;left:566px;display:flex;gap:12px}
.dots i{width:8px;height:8px;border-radius:50%;background:var(--white);display:block}
/* what */
.what{top:540px;height:552px;background:var(--light)}
.what p{position:absolute;left:200px;width:800px;text-align:center;font-size:14px;line-height:25px;color:#555}
.btn-dark{position:absolute;left:524px;top:450px;width:152px;height:38px;line-height:38px;background:var(--btn);color:var(--white);font-size:13px;font-weight:500;text-align:center}
/* benefits */
.benefits{top:1092px;height:615px}
.benefit{position:absolute;width:240px}
.benefit b{position:absolute;left:0;top:0;width:40px;height:40px;background:var(--cyan);color:var(--white);font-weight:400;font-size:28px;text-align:center;line-height:40px}
.benefit p{position:absolute;left:52px;top:0;width:190px;font-size:11.5px;line-height:17px;color:#555}
/* reviews */
.reviews{top:1707px;height:503px;background:var(--sky)}
.review-photo{position:absolute;left:0;top:0;width:430px;height:503px;background:radial-gradient(ellipse at 55% 45%,#f3f3f3 0%,#cfe6ef 45%,#8fcde3 80%)}
.review-card{position:absolute;left:434px;top:206px;width:653px;height:208px;background:var(--card);color:var(--white);padding:28px 34px}
.review-card h3{font-size:26px;font-weight:500}
.review-card small{display:block;font-size:11px;color:#ccc;margin-top:2px}
.review-card .line{width:590px;height:1px;background:#555;margin:10px 0 12px}
.review-card p{font-size:13px;line-height:22px}
/* how */
.how{top:2210px;height:438px}
.step{position:absolute;top:208px;width:110px;height:110px;border-radius:50%;background:var(--cyan)}
.step.first{background:#2a2a2a}
.step svg{position:absolute;left:35px;top:22px}
.step em{position:absolute;left:0;width:110px;top:78px;text-align:center;color:var(--ink);font-style:normal;font-size:10px;font-weight:700}
.step.first em{color:var(--white)}
.step-label{position:absolute;top:350px;width:220px;text-align:center;font-size:14px;font-weight:700;color:var(--ink)}
/* case */
.case{top:2648px;height:389px;background:linear-gradient(180deg,#1b1b1b,#0c0c0c)}
.case .title{color:var(--white)}
.case .sub{position:absolute;top:105px;left:0;width:1200px;text-align:center;font-size:13px;color:#bbb}
.stat{position:absolute;top:235px;width:200px;text-align:center;color:var(--white)}
.stat strong{display:block;font-weight:300;font-size:48px;color:#cfe9f0}
.stat span{display:block;font-size:13px;margin-top:6px}
/* contact */
.contact{top:3037px;height:452px}
.field{position:absolute;width:340px;border-bottom:1px solid #ddd;padding-bottom:12px;font-size:11px;font-weight:500;color:#333;letter-spacing:.5px}
/* footer */
.footer{top:3489px;height:277px;background:var(--dark);color:#aaa;font-size:12px}
.footer h4{color:var(--cyan);font-size:13px;font-weight:700;margin-bottom:14px}
.footer .col{position:absolute;top:50px;line-height:25px}
.footer-brand{position:absolute;left:148px;top:70px;width:110px;text-align:center;color:var(--white)}
.footer-brand .dot{display:block;margin:0 auto 8px;width:54px;height:54px;border-radius:50%;background:var(--orb)}
.footer-brand span{font-size:14px;letter-spacing:1px;font-weight:500}
.contact-row{display:flex;align-items:center;gap:10px}
.contact-row i{width:20px;height:20px;border-radius:50%;background:var(--cyan);display:inline-block}
.copy{position:absolute;left:0;top:246px;width:1200px;border-top:1px solid #2a2a2a;padding-top:8px;text-align:center;font-size:10px;color:#888}
</style>
</head>
<body>

<section class="hero">
  <div class="hero-photo" role="img" aria-label="Aerial photograph of a city skyline along a river at sunset"></div>
  <nav class="nav">
    <a class="active" style="left:190px">WHAT WE DO</a>
    <a style="left:314px">BENEFITS</a>
    <a style="left:412px">TESTIMONIALS</a>
    <div class="brand"><span class="dot"></span><span>VOSTRELINK</span></div>
    <a style="left:683px">HOW IT WORKS</a>
    <a style="left:818px">CASE STUDY</a>
    <a style="left:940px">CONTACT</a>
    <div class="search"><svg width="32" height="32" viewBox="0 0 32 32"><circle cx="14" cy="14" r="6" fill="none" stroke="#fff" stroke-width="2"/><line x1="18.5" y1="18.5" x2="23" y2="23" stroke="#fff" stroke-width="2"/></svg></div>
  </nav>
  <h1>Vostrelink exceeds all expectations for Shopping Centre Managers,<br>Shoppers, Tenants and Landlords</h1>
  <div class="btn-cyan" style="left:524px;top:368px;width:152px;height:36px;line-height:36px">LEARN MORE</div>
  <div class="dots"><i></i><i></i><i></i><i></i></div>
</section>

<section class="what">
  <h2 class="title" style="top:64px">WHAT WE CAN DO FOR YOU</h2>
  <div class="orb" style="top:125px"></div>
  <p style="top:196px">Vostrelink provides shopping centre managers with an easy to use platform which enables them to delight their shoppers, impress their tenants, provide detailed data to their landlords and all accessible to them at the click of button.</p>
  <p style="top:266px">Vostrelink gives shopping centres real time tracking through smart ID's of individual customer journeys through their physical stores, enabling highly targeted, relevant and timely promotional and rewarding capabilities. Furthermore, through deep analytical data processing of the customer journey, centre managers will be able to more accurately and reliably predict shopping behaviours.</p>
  <p style="top:358px">The potential benefits that Vostrelink offer shopping centres are huge. Vostrelink can enhance consumers' experience and simultaneously gather discrete, detailed location data that can be used to map shopping habits and staff activity.</p>
  <div class="btn-dark">READ MORE</div>
</section>

<section class="benefits">
  <h2 class="title" style="top:50px">OUR BENEFITS</h2>
  <div class="orb" style="top:115px"></div>
  <div class="benefit" style="left:75px;top:200px"><b>1</b><p>Increase dwell times by setting triggers which send text messages rewarding loyalty E.g. if a shopper has been in the centre for an hour or more, an automatic text will be sent giving the shopper an reward such as free park or a free coffee.</p></div>
  <div class="benefit" style="left:351px;top:200px"><b>2</b><p>Provide undisputable proof to your tenants of marketing R.O.I E.g. You can provide metrics that prove out of the 1,000 targeted messages sent to their customers, within the past week, 350 stopped and entered their store. You can show them who their best customers were, how long they stayed in their stores and where they came from etc</p></div>
  <div class="benefit" style="left:622px;top:200px"><b>3</b><p>Lower marketing costs by only directly marketing (text message) to your tenants ideal customer segment while they are shopping near their store.</p></div>
  <div class="benefit" style="left:896px;top:200px"><b>4</b><p>Increase and measure customer loyalty through tailored targeted rewards and analytics.</p></div>
  <div class="benefit" style="left:75px;top:455px"><b>5</b><p>Easy to install, no wiring required.</p></div>
  <div class="benefit" style="left:351px;top:455px"><b>6</b><p>Easy to use dashboard with one click reporting.</p></div>
  <div class="benefit" style="left:622px;top:455px"><b>7</b><p>Know who your customers are personally and when they visit you.</p></div>
  <div class="benefit" style="left:896px;top:455px"><b>8</b><p>Have the data to back up any decision's you make.</p></div>
</section>

<section class="reviews">
  <div class="review-photo" role="img" aria-label="Portrait photograph of a smiling man in a white shirt with arms crossed"></div>
  <h2 class="title" style="top:70px;left:160px;width:880px">CUSTOMERS REVIEWS</h2>
  <div class="orb" style="top:130px;left:582px"></div>
  <div class="review-card">
    <h3>Daniel Hart</h3>
    <small>Riverside Centre Manager</small>
    <div class="line"></div>
    <p>"All of the data captured has now been analysed, equipping us with invaluable insights into shopping and spending patterns, and the impact of our media campaigns – all of which is gold dust as we plan ahead for future focussed campaigns. The flexibility of the Vostrelink operating platform software means we will most certainly use this system again going forward."</p>
  </div>
</section>

<section class="how">
  <h2 class="title" style="top:72px">HOW IT WORKS</h2>
  <div class="orb" style="top:134px"></div>
  <svg class="abs" style="left:0;top:0" width="1200" height="438" viewBox="0 0 1200 438">
    <g fill="none" stroke="#ccc" stroke-width="2">
      <path d="M272 300 Q300 318 330 298"/><path d="M467 300 Q495 318 525 298"/>
      <path d="M662 300 Q690 318 720 298"/><path d="M858 300 Q886 318 914 298"/>
    </g>
  </svg>
  <div class="step first" style="left:158px"><svg width="40" height="40" viewBox="0 0 40 40" fill="none" stroke="#fff" stroke-width="2"><rect x="6" y="8" width="28" height="24" rx="3"/><circle cx="20" cy="18" r="5"/><path d="M12 29c2-5 14-5 16 0"/></svg><em>STEP1</em></div>
  <div class="step" style="left:352px"><svg width="40" height="40" viewBox="0 0 40 40" fill="none" stroke="#111" stroke-width="2"><rect x="12" y="5" width="16" height="30" rx="3"/><line x1="18" y1="30" x2="22" y2="30"/></svg><em>STEP 2</em></div>
  <div class="step" style="left:547px"><svg width="40" height="40" viewBox="0 0 40 40" fill="none" stroke="#111" stroke-width="2"><rect x="6" y="6" width="28" height="28"/><path d="M12 28l16-16M14 14h4M24 24h4"/></svg><em>STEP 3</em></div>
  <div class="step" style="left:743px"><svg width="40" height="40" viewBox="0 0 40 40" fill="none" stroke="#111" stroke-width="2"><path d="M20 5l13 5v9c0 9-6 14-13 16C13 33 7 28 7 19v-9z"/><path d="M14 20l4 4 8-8"/></svg><em>STEP 4</em></div>
  <div class="step" style="left:934px"><svg width="40" height="40" viewBox="0 0 40 40" fill="none" stroke="#111" stroke-width="2"><circle cx="20" cy="20" r="14"/><ellipse cx="20" cy="20" rx="6" ry="14"/><line x1="6" y1="20" x2="34" y2="20"/></svg><em>STEP 5</em></div>
  <div class="step-label" style="left:103px">ALLOCATE CARDS</div>
  <div class="step-label" style="left:297px">DIRECT MARKETING</div>
  <div class="step-label" style="left:492px">REWARDING LOYALTY</div>
  <div class="step-label" style="left:688px">COLLECT DATA</div>
  <div class="step-label" style="left:879px">DATA ANALYTICS</div>
</section>

<section class="case" role="img" aria-label="Dark blurred photograph of a shopping centre interior">
  <h2 class="title" style="top:58px">CASE STUDY</h2>
  <div class="sub">Results from a 31 day campaign</div>
  <div class="orb" style="top:140px"></div>
  <div class="stat" style="left:46px"><strong>650</strong><span>VIP Card Holders</span></div>
  <div class="stat" style="left:226px"><strong>10500</strong><span>Messages Sent</span></div>
  <div class="stat" style="left:410px"><strong>22%</strong><span>Conversion Rate</span></div>
  <div class="stat" style="left:578px"><strong>1.2Hrs</strong><span>AVG Dwell Time</span></div>
  <div class="stat" style="left:766px"><strong>95%</strong><span>Tenant Engagement</span></div>
  <div class="stat" style="left:954px"><strong>980</strong><span>Loyalty Rewards Issued</span></div>
</section>

<section class="contact">
  <h2 class="title" style="top:72px">CONTACT US</h2>
  <div class="orb" style="top:120px"></div>
  <div class="field" style="left:248px;top:222px;width:340px">YOUR NAME</div>
  <div class="field" style="left:612px;top:222px;width:340px">YOUR MESSAGE</div>
  <div class="field" style="left:248px;top:300px;width:340px">YOUR E-MAIL</div>
  <div class="field" style="left:612px;top:300px;width:340px;color:transparent">.</div>
  <div class="btn-cyan" style="left:522px;top:370px;width:156px;height:38px;line-height:38px">SUBMIT</div>
</section>

<footer class="footer">
  <div class="footer-brand"><span class="dot"></span><span>VOSTRELINK</span></div>
  <div class="col" style="left:319px">
    <h4>QUICK LINKS</h4>
    What we do<br>Benefits<br>Testimonials<br>How it works<br>Case study<br>Contact
  </div>
  <div class="col" style="left:520px">
    <h4>ADDRESS</h4>
    Unit 7, Harbour Road,<br>Kilmore, KT12 4RP<br>hello@vostrelink.com
  </div>
  <div class="col" style="left:773px">
    <h4>CONTACT INFO</h4>
    <div class="contact-row"><i></i>0210 555 0148</div>
    <div class="contact-row" style="margin-top:8px"><i></i>contact@vostrelink.com</div>
  </div>
  <div class="copy">© 2018 Company Name | All Rights Reserved</div>
</footer>

</body>
</html>
```